Custom Manufacturing Company square space website design

I own a custom manufacturing company that uses precision cutting technology to manufacture project components over a couple industries. We have an industrial CNC router and state of the art edge bander and cut a lot of cabinetry components for cabinet shops, builders, closet companies, ect. We offer design and assembly for any cabinetry or can build cabinets to spec. We also cut components for other industries out of wood, plastics, acryclics, ect. We offer design engineering services, product development protype services. we have a 3D printer farm. We want our communicate trust, dependability, and the value we place on client relationships.

We essentially want a credibility website. Landing page and drops downs for services we offer, capabilites, about us, contact

```html
<!DOCTYPE html>
<html lang="en">
<head>
<meta charset="utf-8">
<title>Northline CNC</title>
<link href="https://fonts.googleapis.com/css2?family=Poppins:wght@400;500;600;700;800&display=swap" rel="stylesheet">
<style>
:root{
  --blue:#1d5589;
  --blue-dark:#154571;
  --blue-soft:#7b9bbb;
  --ink:#111111;
  --navy:#0e1a26;
  --text:#222;
  --white:#fff;
}
*{margin:0;padding:0;box-sizing:border-box}
html,body{width:1200px;height:3993px;overflow:hidden}
body{font-family:"Poppins",sans-serif;color:var(--text);background:var(--white);position:relative}
.abs{position:absolute}

/* header */
.topbar{left:561px;top:0;width:639px;height:65px;background:var(--navy);clip-path:polygon(0 0,100% 0,100% 100%,38px 100%);color:#fff;font-size:15px}
.topbar span{position:absolute;top:21px;display:flex;align-items:center;gap:8px;white-space:nowrap}
.brand{left:96px;top:20px;width:196px;text-align:center}
.brand .mark{width:66px;height:46px;border:2px solid #333;margin:0 auto 12px}
.brand .name{font-weight:600;font-size:17px;letter-spacing:2px;color:#222;white-space:nowrap}
.nav{top:88px;left:530px;display:flex;gap:33px;font-size:15px;color:#333;white-space:nowrap}
.nav .active{font-weight:600;color:var(--blue-dark);border-bottom:2px solid var(--blue-dark);padding-bottom:2px}

/* hero */
.hero{left:0;top:129px;width:1200px;height:693px;background:linear-gradient(180deg,#3f1f0d 0%,#6e3a1a 12%,#8a4c25 24%,#5a2d13 38%,#a89680 46%,#c4b7a5 52%,#9c8a74 58%,#d8d2c8 63%,#7a4421 68%,#8c5128 82%,#5a2c12 100%)}
.hero-pill{left:225px;top:434px;width:752px;height:256px;border-radius:128px;background:rgba(29,85,137,.88);color:#fff;text-align:center}
.hero-pill .kicker{margin-top:36px;font-weight:700;font-size:19px}
.hero-pill h1{font-size:62px;font-weight:800;line-height:1.1;margin-top:10px}
.hero-pill p{font-size:16px;line-height:28px;margin-top:10px}

/* about */
.about-photo{left:181px;top:992px;width:342px;height:342px;border-radius:50%;background:linear-gradient(120deg,#efe6da 0%,#d4b08a 30%,#b87d4c 55%,#9a6234 80%,#6e4222 100%)}
.about-ring{left:170px;top:985px}
.section-title{font-weight:800;color:var(--blue-dark);font-size:44px}
.about-title{left:639px;top:915px}
.about-text{left:639px;top:983px;width:470px;font-size:15.5px;line-height:33.5px;color:#222}
.btn{display:inline-block;background:var(--ink);color:#fff;font-size:15px;padding:11px 21px;border-radius:6px}
.about-btn{left:639px;top:1382px}

/* services */
.services{left:0;top:1605px;width:1200px;height:686px;background:linear-gradient(90deg,#1e5a90,#2b6aa0 60%,#1d5589)}
.services-photo{left:0;top:1605px}
.services-title{left:640px;top:1718px;color:#fff;font-size:44px;font-weight:800}
.services-text{left:640px;top:1782px;width:460px;color:#fff;font-size:15.5px;line-height:25.7px}
.services-btn{left:640px;top:2135px}

/* testimonials */
.testi-title{left:0;top:2362px;width:1200px;text-align:center}
.card{border:2px solid var(--blue);border-radius:18px;background:#fff;text-align:center;font-size:20px;line-height:34.5px;color:#222}
.card::after{content:"";position:absolute;left:50%;bottom:-14px;width:24px;height:24px;background:#fff;border-right:2px solid var(--blue);border-bottom:2px solid var(--blue);transform:translateX(-50%) rotate(45deg)}
.card-main{left:368px;top:2438px;width:466px;height:195px;padding:26px 20px}
.card-side{top:2470px;width:256px;height:156px;font-size:14px;line-height:27.5px;color:#666;border-color:var(--blue-soft);padding:21px 12px;white-space:nowrap}
.card-side::after{border-color:var(--blue-soft);width:18px;height:18px;bottom:-11px}
.quote{font-family:Georgia,serif;font-size:110px;font-weight:700;color:var(--blue);line-height:1}
.avatar{border-radius:50%;background:linear-gradient(180deg,#dfe5ea,#9fb2c2);border:3px solid #fff;box-shadow:0 0 0 3px var(--blue)}
.arrow{width:34px;height:34px;background:var(--blue);border-radius:3px;display:flex;align-items:center;justify-content:center}

/* contact */
.contact{left:0;top:2889px;width:1200px;height:684px;background:radial-gradient(ellipse at 50% 40%,#1a1a1a,#0b0b0b 80%)}
.contact h2{position:absolute;top:88px;width:1200px;text-align:center;color:#fff;font-size:44px;font-weight:800}
.contact .lead{position:absolute;top:160px;width:1200px;text-align:center;color:#fff;font-size:16px;line-height:27px}
.info{color:#fff;font-size:16px;display:flex;align-items:center;gap:12px;line-height:26px;white-space:nowrap}
.field{border:2px solid #fff;border-radius:6px;color:#fff;font-size:16px;padding:14px 17px}
.submit{border:2px solid #fff;border-radius:6px;color:#fff;font-size:15px;width:130px;height:45px;display:flex;align-items:center;justify-content:center}

/* footer */
.footer{left:0;top:3573px;width:1200px;height:420px;background:linear-gradient(180deg,#1b5a92,#245f96)}
.footer .fbrand{position:absolute;left:0;top:80px;width:1200px;text-align:center;color:#fff}
.fbrand .mark{width:80px;height:56px;border:2px solid #fff;margin:0 auto 12px}
.fbrand .name{font-weight:600;font-size:22px;letter-spacing:4px}
.fnav{position:absolute;top:197px;width:1200px;display:flex;justify-content:center;gap:21px;color:#fff;font-size:16px}
.social{position:absolute;top:250px;width:1200px;display:flex;justify-content:center;gap:22px;color:#fff;font-size:14px}
.fline{position:absolute;left:112px;top:327px;width:975px;height:1px;background:rgba(255,255,255,.6)}
.copy{position:absolute;top:370px;width:1200px;text-align:center;color:#fff;font-size:16px}
</style>
</head>
<body>

<header>
  <div class="abs topbar">
    <span style="left:74px"><svg width="13" height="13" viewBox="0 0 14 14"><rect x="1" y="3" width="12" height="8" fill="none" stroke="#fff" stroke-width="1.4"/><path d="M1 3l6 5 6-5" fill="none" stroke="#fff" stroke-width="1.4"/></svg>info@northlinecnc.example</span>
    <span style="left:347px"><svg width="13" height="13" viewBox="0 0 14 14"><circle cx="7" cy="7" r="5.5" fill="none" stroke="#fff" stroke-width="1.4"/><circle cx="7" cy="7" r="2" fill="#fff"/></svg>1234 Lorem Ipsum st</span>
  </div>
  <div class="abs brand"><div class="mark"></div><div class="name">NORTHLINE CNC</div></div>
  <nav class="abs nav"><span class="active">Home</span><span>About Us</span><span>Services We Offer</span><span>Capabilities</span><span>Contact Us</span></nav>
</header>

<section class="abs hero" role="img" aria-label="Photo of a kitchen with dark wooden cabinets and tiled backsplash"></section>
<svg class="abs" style="left:0;top:660px" width="1200" height="170" viewBox="0 0 1200 170">
  <path d="M0 20 C300 180 900 180 1200 20 L1200 170 L0 170 Z" fill="#fff"/>
  <path d="M95 68 C350 170 850 170 1080 76 C850 155 370 160 95 68 Z" fill="#111"/>
</svg>
<div class="abs hero-pill">
  <div class="kicker">WELCOME TO</div>
  <h1>NORTHLINE CNC</h1>
  <p>Lorem ipsum dolor sit amet, consectetur adipiscing elit, sed do eiusmod<br>tempor incididunt ut labore et dolore magna aliqua. Quis ipsum suspendisse</p>
</div>

<section class="about">
  <svg class="abs about-ring" width="360" height="360" viewBox="0 0 360 360"><path d="M180 8 A172 172 0 0 1 300 300" fill="none" stroke="#1d5589" stroke-width="5"/></svg>
  <div class="abs about-photo" role="img" aria-label="Photo of built-in light wood cabinetry under a staircase"></div>
  <h2 class="abs section-title about-title">ABOUT US</h2>
  <p class="abs about-text">Lorem ipsum dolor sit amet, consectetur adipiscing elit, sed do eiusmod tempor incididunt ut labore et dolore magna aliqua. Quis ipsum suspendisse ultrices gravida. Risus commodo viverra maecenas accumsan lacus vel facilisis. Lorem ipsum dolor sit amet, consectetur adipiscing elit, sed do eiusmod tempor incididunt ut labore et dolore magna aliqua. Quis ipsum suspendisse ultrices gravida. Risus commodo viverra maecenas accumsan lacus vel facilisis. Lorem ipsum dolor sit amet, consectetur adipiscing elit, sed do eiusmod tempor incididunt ut labore et dolore magna aliqua. Quis ipsum suspendisse ultrices gravida. Risus</p>
  <span class="abs btn about-btn">READ MORE</span>
</section>

<section>
  <div class="abs services"></div>
  <svg class="abs services-photo" width="610" height="686" viewBox="0 0 610 686" role="img" aria-label="Photo of white kitchen drawers with metal pulls above a wood floor">
    <defs><linearGradient id="svcGrad" x1="0" y1="0" x2="0.6" y2="1"><stop offset="0" stop-color="#7a6a58"/><stop offset=".2" stop-color="#cfcfcb"/><stop offset=".5" stop-color="#f1f1ee"/><stop offset=".72" stop-color="#d9d8d4"/><stop offset=".85" stop-color="#9a6a40"/><stop offset="1" stop-color="#6a4526"/></linearGradient></defs>
    <path d="M0 0 H440 C560 80 610 220 600 350 C592 500 530 630 460 686 H0 Z" fill="url(#svcGrad)"/>
  </svg>
  <h2 class="abs services-title">SERVICES WE OFFER</h2>
  <p class="abs services-text">Lorem ipsum dolor sit amet, consectetur adipiscing elit, sed do eiusmod tempor incididunt ut labore et dolore magna aliqua. Quis ipsum suspendisse ultrices gravida. Risus commodo viverra maecenas accumsan lacus vel facilisis. Lorem ipsum dolor sit amet, consectetur adipiscing elit, sed do eiusmod tempor incididunt ut labore et dolore magna aliqua. Quis ipsum suspendisse ultrices gravida. Risus commodo viverra maecenas accumsan lacus vel facilisis. Lorem ipsum dolor sit amet, consectetur adipiscing elit, sed do eiusmod tempor incididunt ut labore et dolore magna aliqua. Quis ipsum suspendisse ultrices gravida. Risus commodo viverra maecenas accumsan lacus vel facilisis.</p>
  <span class="abs btn services-btn">READ MORE</span>
</section>

<section>
  <h2 class="abs section-title testi-title">TESTIMONIALS</h2>
  <div class="abs card card-side" style="left:0">Lorem ipsum dolor sit amet,<br>consectetur adipiscing elit,<br>sed do eiusmod tempor<br>incididunt ut labore et</div>
  <div class="abs quote" style="left:233px;top:2500px;font-size:80px;color:#6d8fb0">&#8221;</div>
  <div class="abs card card-side" style="left:944px">Lorem ipsum dolor sit amet,<br>consectetur adipiscing elit,<br>sed do eiusmod tempor<br>incididunt ut labore et</div>
  <div class="abs quote" style="left:922px;top:2500px;font-size:80px;color:#6d8fb0">&#8220;</div>
  <div class="abs card card-main">Lorem ipsum dolor sit amet, consecte-<br>tur adipiscing elit, sed do eiusmod<br>tempor incididunt ut labore et dolore<br>magna aliqua. Quis ipsum sus-</div>
  <div class="abs quote" style="left:340px;top:2490px">&#8220;</div>
  <div class="abs quote" style="left:803px;top:2490px">&#8221;</div>
  <div class="abs avatar" style="left:36px;top:2658px;width:70px;height:70px" role="img" aria-label="Customer portrait"></div>
  <div class="abs avatar" style="left:556px;top:2672px;width:88px;height:88px" role="img" aria-label="Customer portrait"></div>
  <div class="abs avatar" style="left:1098px;top:2658px;width:70px;height:70px" role="img" aria-label="Customer portrait"></div>
  <div class="abs arrow" style="left:550px;top:2792px"><svg width="12" height="12" viewBox="0 0 12 12"><path d="M8 1L3 6l5 5" fill="none" stroke="#fff" stroke-width="1.8"/></svg></div>
  <div class="abs arrow" style="left:618px;top:2792px"><svg width="12" height="12" viewBox="0 0 12 12"><path d="M4 1l5 5-5 5" fill="none" stroke="#fff" stroke-width="1.8"/></svg></div>
</section>

<section class="abs contact">
  <h2>GET IN TOUCH</h2>
  <p class="lead">Lorem ipsum dolor sit amet, consectetur adipiscing elit, sed do eiusmod tempor incididunt ut labore et dolore magna aliqua.<br>Quis ipsum suspendisse ultrices gravida. Risus commodo viverra maecenas accumsan lacus vel facilisis.</p>
  <div class="abs info" style="left:152px;top:259px"><svg width="14" height="14" viewBox="0 0 14 14"><rect x="1" y="3" width="12" height="8" fill="none" stroke="#fff" stroke-width="1.3"/><path d="M1 3l6 5 6-5" fill="none" stroke="#fff" stroke-width="1.3"/></svg>info@northlinecnc.example</div>
  <div class="abs info" style="left:525px;top:245px"><svg width="14" height="14" viewBox="0 0 14 14"><path d="M7 1a4.5 4.5 0 0 1 4.5 4.5C11.5 9 7 13 7 13S2.5 9 2.5 5.5A4.5 4.5 0 0 1 7 1z" fill="none" stroke="#fff" stroke-width="1.3"/><circle cx="7" cy="5.5" r="1.5" fill="#fff"/></svg><span>1234 Lorem Ipsum st<br>Lorem Ipsum st</span></div>
  <div class="abs info" style="left:892px;top:259px"><svg width="14" height="14" viewBox="0 0 14 14"><path d="M3 1.5l2.2 2.6-1.2 1.6c.8 1.8 2.4 3.4 4.3 4.3l1.6-1.2 2.6 2.2-1.3 1.6C6.6 12.4 1.6 7.4 1.4 2.8z" fill="none" stroke="#fff" stroke-width="1.2"/></svg>+1 888 888 8888</div>
  <div class="abs field" style="left:110px;top:336px;width:431px;height:54px">Name</div>
  <div class="abs field" style="left:110px;top:426px;width:431px;height:54px">Email</div>
  <div class="abs field" style="left:110px;top:515px;width:431px;height:54px">Phone Number</div>
  <div class="abs field" style="left:658px;top:336px;width:431px;height:157px">Message</div>
  <div class="abs submit" style="left:658px;top:520px">SUBMIT</div>
</section>

<footer class="abs footer">
  <div class="fbrand"><div class="mark"></div><div class="name">NORTHLINE CNC</div></div>
  <nav class="fnav"><span>Home</span><span>About Us</span><span>Services We Offer</span><span>capabilities</span><span>Contact Us</span></nav>
  <div class="social" aria-label="Social media links"><span>Feed</span><span>Page</span><span>Photos</span><span>Clips</span><span>Channel</span></div>
  <div class="fline"></div>
  <div class="copy">© 2023 &nbsp;Northline CNC</div>
</footer>

</body>
</html>
```